Probate (Legal) Wordpress Design with Coding for Online Company

I need a Wordpress design with coding, pictures, content to be provided by me, fully responsive, and development. This is for a 6-7 page design.

Pages Needed: Home/About/Probate/Process/FAQ/Contact Us/Blog.

The home page should be organized as followed:
-Steps in Probate: Gather; Implement; Close (each step will come with content)
-Flat-Fee Price & Savings: Content will go here with a button to contact us (phone number) or just the phone number.
-You Have Questions, We Have Answers: five questions with content. Only one question answer to show at a time when clicked on the question from the list.
-Get to Know Us: a brief description with content about what we do and who we are.

Main image slogan: Helping Californians deal with loss with DIGNITY & UNDERSTATING (you may use a better slogan if you wish).

The Contact page should not have a map since we are an online company. We service the entire state of California in every county and city.

The About page should be simple, direct, and easy on the eye. It should have a brief description of who we are and it should have no more than 6 reasons why the client should hire us.

About our online California company. We are not attorneys but legal document assistants who prepare legal documents for probate estate when someone dies with or without a will and assets need to be distributed. We have a flat-fee for Formal Probate of $999 and $699 for Informal Probate. We are an online company and offer our services to the entire state of California in every county. We do everything over the phone and email. The turn around time for us to prepare the initial legal paperwork for the client is within 3-5 business days. We can prepare, file, serve and manage a probate matter from petition to closing. We are not attorneys so our prices are very affordable compare to the attorney.

The company name for the website will be www.velmarhollow.com, The Velmar Hollow Group.

I do not have a logo yet. The colors of the website should be easy on the eye and calming. THE SITE SHOULD BE SIMPLE AND STRAIGHT TO THE POINT. EASY TO NAVIGATE.

The company phone number should be very visible and should stand out to the client. It should also be clickable and ready to dial for smartphone users.

I do not want a contact form on the homepage. THE MAIN THING IS FOR THE POTENTIAL CLIENT TO CALL OUR OFFICE TO SIGN UP.

I do like some images of family or people since we are dealing with people who just lost a loved one. Not all the images have to be of people.

The site should not look like we practice law or that people can mistake us for attorneys.

Target Market(s)

People who just lost a loved one who had property, assets, in California but died with or without a will or trust. This is for people looking to hire non-attorneys.

Coding

Coded - Design and coding required

Font styles to use
Serif

Colors

Designer to choose colors to be used in the design.

Requirements
Must have
• Refer to Project Description.
Nice to have
• The sample images provided is what I am attracted to for the homepage image.
Should not have

```html
<!DOCTYPE html>
<html lang="en">
<head>
<meta charset="utf-8">
<title>The Velmar Hollow Group</title>
<link href="https://fonts.googleapis.com/css2?family=PT+Serif:wght@400;700&family=Open+Sans:wght@400;600&display=swap" rel="stylesheet">
<style>
:root{
  --red:#e3212f;
  --red-deep:#c9293a;
  --ink:#1b1b1b;
  --text:#555;
  --muted:#777;
  --line:#dcdcdc;
  --white:#fff;
}
*{box-sizing:border-box;margin:0;padding:0}
html,body{width:1200px;height:2821px;overflow:hidden;background:var(--white)}
body{font-family:"Open Sans",Arial,sans-serif;color:var(--text);position:relative}
.serif{font-family:"PT Serif",Georgia,serif}
a{color:inherit;text-decoration:none}

/* header */
.site-header{position:absolute;top:0;left:0;width:1200px;height:105px}
.brand{position:absolute;left:88px;top:30px;display:flex;align-items:center;gap:12px;font-family:"PT Serif",Georgia,serif;font-weight:700;font-size:22px;color:var(--red)}
.brand-mark{width:26px;height:26px;border-radius:50%;background:var(--red)}
.top-contact{position:absolute;right:30px;top:16px;display:flex;align-items:center;gap:30px;font-family:"PT Serif",Georgia,serif;font-size:15px;color:var(--ink)}
.top-contact span{display:flex;align-items:center;gap:8px}
.btn-solid{background:var(--red);color:var(--white);border-radius:6px;padding:8px 26px;font-weight:700}
.main-nav{position:absolute;right:28px;top:72px;display:flex;gap:28px;font-family:"PT Serif",Georgia,serif;font-weight:700;font-size:15px;color:var(--ink)}
.main-nav .active{color:var(--red)}

/* hero */
.hero{position:absolute;top:105px;left:0;width:1200px;height:527px;background:linear-gradient(100deg,#3a2c22 0%,#8a7455 35%,#cfc3ad 60%,#a9a08f 80%,#6e6a62 100%)}
.hero h1{position:absolute;left:97px;top:195px;font-family:"PT Serif",Georgia,serif;font-size:41px;line-height:48px;color:var(--white);font-weight:700;text-shadow:0 2px 4px rgba(0,0,0,.35)}
.hero .btn-solid{position:absolute;left:98px;top:311px;font-family:"PT Serif",Georgia,serif;font-size:18px;padding:12px 24px}
.dots{position:absolute;left:578px;top:473px;display:flex;gap:4px}
.dots i{width:9px;height:9px;border-radius:50%;border:1.5px solid var(--red);background:transparent}
.dots i:first-child{background:var(--red)}

/* steps */
.steps{position:absolute;top:632px;left:0;width:1200px;height:573px}
.steps h2{position:absolute;left:97px;top:78px;font-family:"PT Serif",Georgia,serif;font-size:28px;color:var(--ink)}
.steps .tagline{position:absolute;left:97px;top:121px;font-size:10px;font-style:italic;color:var(--ink)}
.steps .intro{position:absolute;left:97px;top:140px;width:530px;font-size:11px;line-height:19px}
.timeline{position:absolute;left:138px;top:190px;width:440px}
.timeline::before{content:"";position:absolute;left:8px;top:14px;height:205px;border-left:2px dotted var(--red)}
.step{position:relative;padding-left:34px;margin-bottom:14px}
.step::before{content:"";position:absolute;left:0;top:3px;width:18px;height:18px;border:2px solid var(--red);border-radius:50%;background:var(--white)}
.step::after{content:"";position:absolute;left:6px;top:9px;width:6px;height:6px;border-radius:50%;background:var(--red)}
.step h3{font-size:16px;font-weight:600;color:var(--red);margin-bottom:6px}
.step p{font-size:11px;line-height:20px}
.steps .photo{position:absolute;left:658px;top:158px;width:442px;height:323px;background:linear-gradient(180deg,#5a6f9b 0%,#e3a158 45%,#6a4d50 65%,#2b2c3a 100%)}

/* price band */
.price{position:absolute;top:1205px;left:0;width:1200px;height:413px;background:linear-gradient(180deg,#cd4651 0%,#c63a47 60%,#b8303f 100%);text-align:center;color:var(--white)}
.price .curve{position:absolute;top:-1px;left:0}
.price h2{position:absolute;top:110px;width:100%;font-family:"PT Serif",Georgia,serif;font-size:27px;font-weight:700}
.price p{position:absolute;top:170px;left:150px;width:900px;font-size:21px;line-height:34px}
.btn-outline{position:absolute;left:521px;top:275px;width:159px;height:47px;border:2px solid var(--white);border-radius:8px;line-height:43px;font-size:19px;font-weight:600}

/* faq */
.faq{position:absolute;top:1618px;left:0;width:1200px;height:518px}
.faq h2{position:absolute;top:80px;width:100%;text-align:center;font-family:"PT Serif",Georgia,serif;font-size:27px;font-weight:700;color:var(--ink)}
.faq .photo{position:absolute;left:98px;top:172px;width:224px;height:255px;border:2px solid var(--ink);background:linear-gradient(180deg,#f2c66d 0%,#e59b46 45%,#7b6a3c 75%,#4a4a2a 100%)}
.faq .answer{position:absolute;left:342px;top:172px;width:294px}
.faq .answer h3{font-size:15px;font-weight:600;color:var(--red);line-height:25px;margin-bottom:14px}
.faq .answer p{font-size:11px;line-height:20px;text-align:justify;padding-left:3px}
.faq-list{position:absolute;left:688px;top:166px;width:440px;list-style:none}
.faq-list::before{content:"";position:absolute;left:8px;top:16px;height:225px;border-left:2px dotted var(--red)}
.faq-list li{position:relative;padding-left:32px;height:56.5px;font-size:15px;font-weight:600;color:var(--ink)}
.faq-list li.open{color:var(--red)}
.faq-list li::before{content:"";position:absolute;left:0;top:2px;width:18px;height:18px;border:2px solid var(--red);border-radius:50%;background:var(--white)}
.faq-list li::after{content:"";position:absolute;left:6px;top:8px;width:6px;height:6px;border-radius:50%;background:var(--red)}

/* about panels */
.about{position:absolute;top:2136px;left:0;width:1200px;height:367px;display:flex}
.panel{position:relative;width:600px;height:367px;color:var(--white);padding:76px 0 0 98px}
.panel.what{background:linear-gradient(180deg,#8f3b45 0%,#9c4650 60%,#8d4048 100%)}
.panel.who{width:600px;padding-left:46px;background:linear-gradient(180deg,#8a96a8 0%,#9aa3b0 55%,#7c8494 100%)}
.panel h2{font-family:"PT Serif",Georgia,serif;font-size:28px;font-weight:400;margin-bottom:16px}
.panel p{width:450px;font-size:11px;line-height:20px;text-align:justify}
.btn-small{display:inline-block;margin-top:26px;border:2px solid var(--white);border-radius:6px;padding:5px 15px;font-size:11px;font-weight:600}

/* footer */
.site-footer{position:absolute;top:2503px;left:0;width:1200px;height:318px}
.col{position:absolute;top:60px}
.col h4{font-size:16px;font-weight:600;color:var(--ink);margin-bottom:14px}
.col p,.col li{font-size:11px;line-height:22px;color:var(--muted)}
.col ul{list-style:none}
.col li{display:flex;align-items:center;gap:6px}
.col.about-col{left:98px;width:340px}
.col.about-col p{padding-left:5px}
.social{display:flex;gap:8px;margin-top:14px}
.social i{width:34px;height:34px;border-radius:50%;border:2px solid var(--red)}
.col.contact-col{left:500px}
.col.news-col{left:801px;width:310px}
.email-field{margin-top:18px;width:295px;height:34px;border:1.5px solid #bbb;border-radius:18px;display:flex;align-items:center;justify-content:space-between;padding:0 16px 0 22px;font-size:11px;color:#999}
.footer-bar{position:absolute;left:98px;right:98px;top:270px;border-top:1px solid var(--line);display:flex;justify-content:space-between;padding-top:14px;font-size:11px;color:var(--muted)}
.footer-bar nav{display:flex;gap:16px}
</style>
</head>
<body>

<header class="site-header">
  <a class="brand" href="#"><span class="brand-mark"></span>The Velmar Hollow Group</a>
  <div class="top-contact">
    <span><svg width="13" height="13" viewBox="0 0 24 24"><path fill="#e3212f" d="M6.6 10.8a15 15 0 0 0 6.6 6.6l2.2-2.2c.3-.3.7-.4 1-.2 1.1.4 2.3.6 3.6.6.6 0 1 .4 1 1V20c0 .6-.4 1-1 1A17 17 0 0 1 3 4c0-.6.4-1 1-1h3.5c.6 0 1 .4 1 1 0 1.3.2 2.5.6 3.6.1.3 0 .7-.2 1z"/></svg>(+1) 555 010 0199</span>
    <span><svg width="15" height="12" viewBox="0 0 24 18"><rect x="1" y="1" width="22" height="16" rx="2" fill="#e3212f"/><path d="M2 2l10 8 10-8" stroke="#fff" stroke-width="2" fill="none"/></svg>mailus@velmarhollow.com</span>
    <a class="btn-solid" href="#">Contact Us</a>
  </div>
  <nav class="main-nav">
    <a class="active" href="#">Home</a><a href="#">About Us</a><a href="#">Testimonials</a><a href="#">Contact Us</a>
    <svg width="15" height="15" viewBox="0 0 24 24"><circle cx="10" cy="10" r="7" stroke="#1b1b1b" stroke-width="3" fill="none"/><path d="M15 15l7 7" stroke="#1b1b1b" stroke-width="3"/></svg>
  </nav>
</header>

<section class="hero" role="img" aria-label="Photo of an advisor meeting a smiling family with a young child on a sofa">
  <h1>Helping Californians deal with loss<br>with Dignity &amp; Understating</h1>
  <a class="btn-solid" href="#">Read More</a>
  <div class="dots"><i></i><i></i><i></i><i></i></div>
</section>

<section class="steps">
  <h2>Steps In Probate</h2>
  <p class="tagline">"Helping Californians deal with loss with DIGNITY &amp; UNDERSTATING"</p>
  <p class="intro">Lorem Ipsum is simply dummy text of the printing and typesetting industry. Lorem Ipsum has been the industry's standard dummy text ever since the 1500s.</p>
  <div class="timeline">
    <div class="step"><h3>Gather</h3><p>Lorem Ipsum is simply dummy text of the printing and typesetting industry. Lorem Ipsum has been the industry's standard dummy text ever since the 1500s.</p></div>
    <div class="step"><h3>Implement</h3><p>Lorem Ipsum is simply dummy text of the printing and typesetting industry. Lorem Ipsum has been the industry's standard dummy text ever since the 1500s.</p></div>
    <div class="step"><h3>Close</h3><p>Lorem Ipsum is simply dummy text of the printing and typesetting industry. Lorem Ipsum has been the industry's standard dummy text ever since the 1500s.</p></div>
  </div>
  <div class="photo" role="img" aria-label="Photo of a city skyline at sunset with light trails on a highway"></div>
</section>

<section class="price" role="img" aria-label="Red tinted photo of a residential street with a family walking">
  <svg class="curve" width="1200" height="30" viewBox="0 0 1200 30" preserveAspectRatio="none"><path d="M0 0H1200V0Q600 40 0 10Z" fill="#fff"/></svg>
  <h2>Flat-Fee Price &amp; Savings</h2>
  <p>Lorem Ipsum is simply dummy text of the printing and typesetting industry. Lorem Ipsum has been the industry's standard dummy text ever since the 1500s.</p>
  <a class="btn-outline" href="#">Contact Us</a>
</section>

<section class="faq">
  <h2>FREQUENTLY ASKED QUESTIONS</h2>
  <div class="photo" role="img" aria-label="Photo of a family playing in a field at sunset"></div>
  <div class="answer">
    <h3>Lorem Ipsum Is Simply Dummy Text of typesetting?</h3>
    <p>Lorem Ipsum is simply dummy text of the printing and typesetting industry. Lorem Ipsum has been the industry's standard dummy text ever since the 1500s, when an un known printer took a galley of type and scrambled it to make a type specimen book. It has survived not only five centuries, but also the leap into electronic typesetting, remaining essentially unchanged.</p>
  </div>
  <ul class="faq-list">
    <li class="open">Lorem Ipsum Is Simply Dummy Text of typesetting?</li>
    <li>Lorem Ipsum Is Simply Dummy Text?</li>
    <li>Lorem Ipsum Is Simply Dummy Text ever?</li>
    <li>Lorem Ipsum Is Simply Dummy Text?</li>
    <li>Lorem Ipsum Is Simply Dummy Text since 1500?</li>
  </ul>
</section>

<section class="about">
  <div class="panel what" role="img" aria-label="Red tinted photo of suburban houses">
    <h2>What we do</h2>
    <p>Lorem Ipsum is simply dummy text of the printing and typesetting industry. Lorem Ipsum has been the industry's standard dummy text ever since the 1500s, when an un known printer took a galley of type and scrambled it to make a type specimen book. It has survived not only five centuries, but also the leap into electronic typesetting, remaining essentially unchanged.</p>
    <a class="btn-small" href="#">Read More</a>
  </div>
  <div class="panel who" role="img" aria-label="Grey tinted photo of a couple reviewing papers with an advisor">
    <h2>Who we Are</h2>
    <p>Lorem Ipsum is simply dummy text of the printing and typesetting industry. Lorem Ipsum has been the industry's standard dummy text ever since the 1500s, when an un known printer took a galley of type and scrambled it to make a type specimen book. It has survived not only five centuries, but also the leap into electronic typesetting, remaining essentially unchanged.</p>
    <a class="btn-small" href="#">Read More</a>
  </div>
</section>

<footer class="site-footer">
  <div class="col about-col">
    <h4>About</h4>
    <p>Duis autem vel eum iriure dolor in hendrerit in vulputate velit esse molestie consequat, vel illum dolore eu feugiat. Duis autem vel eum iriure dolor in hendrerit in vulputate velit esse molestie consequat.</p>
    <div class="social"><i></i><i></i><i></i><i></i></div>
  </div>
  <div class="col contact-col">
    <h4>Contact</h4>
    <ul>
      <li><svg width="9" height="12" viewBox="0 0 12 16"><path fill="#e3212f" d="M6 0a6 6 0 0 0-6 6c0 4.5 6 10 6 10s6-5.5 6-10a6 6 0 0 0-6-6zm0 8.5A2.5 2.5 0 1 1 6 3.5a2.5 2.5 0 0 1 0 5z"/></svg>The Velmar Hollow Group,</li>
      <li style="padding-left:15px">Lorem Ipsum is Simply Dummy.</li>
      <li><svg width="9" height="12" viewBox="0 0 12 16"><path fill="#e3212f" d="M6 0a6 6 0 0 0-6 6c0 4.5 6 10 6 10s6-5.5 6-10a6 6 0 0 0-6-6zm0 8.5A2.5 2.5 0 1 1 6 3.5a2.5 2.5 0 0 1 0 5z"/></svg>mailus@velmarhollow.com</li>
      <li><svg width="10" height="10" viewBox="0 0 24 24"><path fill="#e3212f" d="M6.6 10.8a15 15 0 0 0 6.6 6.6l2.2-2.2c.3-.3.7-.4 1-.2 1.1.4 2.3.6 3.6.6.6 0 1 .4 1 1V20c0 .6-.4 1-1 1A17 17 0 0 1 3 4c0-.6.4-1 1-1h3.5c.6 0 1 .4 1 1 0 1.3.2 2.5.6 3.6.1.3 0 .7-.2 1z"/></svg>(+1) 555 010 0199</li>
    </ul>
  </div>
  <div class="col news-col">
    <h4>Subscribe To Newsletter</h4>
    <p>Hendrerit vulputate velit esse molestie soluta consafg bxf esatv quat velillum nobis.</p>
    <div class="email-field">Your Email Address<svg width="18" height="13" viewBox="0 0 24 18"><rect x="1" y="1" width="22" height="16" rx="2" stroke="#e3212f" stroke-width="2" fill="none"/><path d="M2 2l10 8 10-8" stroke="#e3212f" stroke-width="2" fill="none"/></svg></div>
  </div>
  <div class="footer-bar">
    <span>Copyright © 2017 The Velmar Hollow Group. All Rights Reserved.</span>
    <nav><a href="#">Home</a><a href="#">About Us</a><a href="#">Testimonials</a><a href="#">Contact Us</a></nav>
  </div>
</footer>

</body>
</html>
```